holloway paving service

Needs to have phone number 0418259730 and email markholloway@brightmail.com.au.
ABN 62318470915
name mark holloway

For all your concreting solutions
Excavation
Exposed & colour concrete
House & shed slabs
Driveways
Landing & steps

Contact Information for Business Card

ph 0418259730
email markholloway@brightmail.com.au.
ABN 62318470915
name mark holloway

```html
<!DOCTYPE html>
<html lang="en">
<head>
<meta charset="utf-8">
<title>Holloway Paving Service — Business Card</title>
<link href="https://fonts.googleapis.com/css2?family=Roboto:wght@400;500;700&display=swap" rel="stylesheet">
<style>
  :root {
    --stage: #d9dadb;
    --card: #eef0f1;
    --accent: #d9411e;
    --accent-deep: #c23516;
    --ink: #2a2a2a;
    --charcoal: #2b2b2b;
    --band-text: #f6d9cf;
  }
  * { margin: 0; padding: 0; box-sizing: border-box; }
  html, body {
    width: 1200px; height: 969px; overflow: hidden;
    background: var(--stage);
    font-family: "Roboto", Arial, sans-serif;
  }
  .card {
    position: absolute; left: 100px; top: 200px;
    width: 1000px; height: 568px;
    background: var(--card);
    box-shadow: 0 10px 30px rgba(0,0,0,0.18);
    border-radius: 4px;
    overflow: hidden;
  }
  .brand {
    position: absolute; left: 86px; top: 206px;
    display: flex; align-items: center;
  }
  .brand-square {
    width: 92px; height: 92px; background: var(--accent);
  }
  .brand-divider {
    width: 2px; height: 118px; background: var(--accent);
    margin: 0 12px 0 34px;
  }
  .brand-text { display: flex; flex-direction: column; align-items: center; }
  .brand-name {
    font-weight: 700; font-size: 25px; color: var(--accent);
    text-transform: uppercase; line-height: 1.15; text-align: center;
  }
  .brand-phone {
    margin-top: 6px; font-weight: 500; font-size: 20px;
    color: var(--accent); letter-spacing: 2px;
    border-top: 2px solid var(--ink); padding-top: 4px;
  }
  .person {
    position: absolute; left: 547px; top: 142px;
  }
  .person-name {
    font-weight: 700; font-size: 34px; color: var(--accent);
    text-transform: uppercase; margin-bottom: 18px;
  }
  .contact-list { list-style: none; }
  .contact-list li {
    display: flex; align-items: center;
    font-size: 24px; color: var(--ink); height: 32px;
  }
  .contact-list svg { width: 18px; height: 18px; margin-right: 16px; flex: none; }
  .abn { margin-top: 18px; font-size: 24px; color: var(--ink); }
  .services-band {
    position: absolute; left: 0; top: 447px; width: 100%; height: 91px;
    background: linear-gradient(90deg, var(--accent-deep), var(--accent) 60%, var(--accent));
  }
  .services-band::after {
    content: ""; position: absolute; right: 0; top: 0;
    width: 286px; height: 100%; background: var(--charcoal);
  }
  .services {
    position: absolute; left: 0; width: 714px; top: 16px;
    text-align: center; color: var(--band-text);
    font-size: 23px; line-height: 31px;
  }
  .band-brand {
    position: absolute; right: 40px; top: 0; height: 100%;
    display: flex; align-items: center; z-index: 1;
  }
  .band-square { width: 28px; height: 28px; background: var(--accent); margin-right: 12px; }
  .band-name { color: #ffffff; font-weight: 700; font-size: 18px; text-transform: uppercase; }
</style>
</head>
<body>
  <div class="card">
    <div class="brand">
      <div class="brand-square"></div>
      <div class="brand-divider"></div>
      <div class="brand-text">
        <div class="brand-name">Holloway Paving<br>Service</div>
        <div class="brand-phone">0418259730</div>
      </div>
    </div>

    <div class="person">
      <div class="person-name">Mark Holloway</div>
      <ul class="contact-list">
        <li>
          <svg viewBox="0 0 24 24" aria-hidden="true"><path fill="#d9411e" d="M6.6 10.8a15.1 15.1 0 0 0 6.6 6.6l2.2-2.2c.3-.3.7-.4 1-.2 1.1.4 2.3.6 3.6.6.6 0 1 .4 1 1V20c0 .6-.4 1-1 1A17 17 0 0 1 3 4c0-.6.4-1 1-1h3.5c.6 0 1 .4 1 1 0 1.3.2 2.5.6 3.6.1.3 0 .7-.2 1z"/></svg>
          0418259730
        </li>
        <li>
          <svg viewBox="0 0 24 24" aria-hidden="true"><rect x="2" y="5" width="20" height="14" rx="1.5" fill="#d9411e"/><path d="M3 6l9 7 9-7" fill="none" stroke="#eef0f1" stroke-width="1.8"/></svg>
          markholloway@brightmail.com.au
        </li>
        <li>
          <svg viewBox="0 0 24 24" aria-hidden="true"><circle cx="12" cy="12" r="10" fill="#d9411e"/><path d="M2 12h20M12 2c3 3 3 17 0 20M12 2c-3 3-3 17 0 20" fill="none" stroke="#eef0f1" stroke-width="1.4"/></svg>
          www.hollowaypaving.com.au
        </li>
      </ul>
      <div class="abn">ABN 62318470915</div>
    </div>

    <div class="services-band">
      <div class="services">
        Excavation | Exposed &amp; colour concrete<br>
        House &amp; shed slabs | Driveways | Landing &amp; steps
      </div>
      <div class="band-brand">
        <div class="band-square"></div>
        <div class="band-name">Holloway Paving</div>
      </div>
    </div>
  </div>
</body>
</html>
```